Marwick Family Chiropractic Stationary

The letterhead and business card must have our logo.
We would like to see the logo used in different ways ( It can be expanded upon in the stationary.)
Please use the the same or similar colors.
Must be eye catching and memorable.
Must be easy to read

Reason: The doctor has been too busy to make any final decisions. He would like to give himself a little more time.

Target Market(s)

Chiropractic Healthcare

Industry/Entity Type

Business

Requirements
Must have
• Dr. Leonard Marwick D.C.
Chiropractor

555-555-0183

417 Birchfield Road, 2nd Floor
Larkspur Hollow, NH 06091

drmarwick@marwickspine.example
www.marwickspine.example
www.facebook.com/MarwickFamilySpine
Should not have
• should not be difficult to read

```html
<!DOCTYPE html>
<html lang="en">
<head>
<meta charset="utf-8">
<title>Marwick Family Chiropractic – Business Cards</title>
<link href="https://fonts.googleapis.com/css2?family=Montserrat:wght@600;700&family=Open+Sans:ital,wght@0,400;0,600;1,700&display=swap" rel="stylesheet">
<style>
  :root {
    --backdrop: #b88c60;
    --label: #1e1a16;
    --card-white: #ffffff;
    --card-brown: #221b14;
    --card-black: #0b0a09;
    --brand-green: #2c9a47;
    --leaf-green: #a6cf5c;
    --olive: #b5a330;
    --bark: #3a2f25;
    --ink: #2a2623;
  }
  * { box-sizing: border-box; margin: 0; padding: 0; }
  html, body { width: 1200px; height: 788px; overflow: hidden; }
  body {
    background: var(--backdrop);
    font-family: "Open Sans", Arial, sans-serif;
    position: relative;
  }
  .sheet-label {
    position: absolute;
    width: 526px;
    text-align: center;
    font-size: 21px;
    color: var(--label);
  }
  .card {
    position: absolute;
    width: 526px;
    height: 300px;
    border-radius: 20px;
    overflow: hidden;
    box-shadow: 0 8px 18px rgba(0,0,0,0.35);
    text-align: center;
  }
  .card--front  { left: 59px;  top: 78px;  background: var(--card-white); }
  .card--back-1 { left: 622px; top: 75px;  background: var(--card-white); }
  .card--back-2 { left: 53px;  top: 446px; background: var(--card-brown); }
  .card--back-3 { left: 622px; top: 446px; background: var(--card-black); }

  .brand-dot {
    position: absolute;
    left: 50%;
    border-radius: 50%;
    transform: translateX(-50%);
  }
  .wordmark {
    position: absolute;
    left: 0; right: 0;
    font-family: "Montserrat", Arial, sans-serif;
    font-weight: 700;
    text-transform: uppercase;
    line-height: 1;
  }
  .wordmark .name { display: block; letter-spacing: 1px; }
  .wordmark .trade { display: block; letter-spacing: 0.5px; }
  .doctor {
    position: absolute; left: 0; right: 0; top: 189px;
    font-family: "Montserrat", Arial, sans-serif;
    font-weight: 600; font-size: 14.5px; color: var(--brand-green);
    line-height: 1;
  }
  .doctor .role { color: var(--ink); font-size: 12px; }
  .contact {
    position: absolute; left: 0; right: 0;
    font-size: 12.5px; color: var(--ink); line-height: 1;
  }
  .contact b { font-style: italic; font-weight: 700; }
  .contact .sep { margin: 0 6px; }
  .color-band {
    position: absolute; left: 0; right: 0; bottom: 0; height: 12px;
    display: flex;
  }
  .color-band span { flex: 1; }
  .web {
    position: absolute; left: 0; right: 0;
    font-size: 15px; line-height: 1;
  }
</style>
</head>
<body>

  <div class="sheet-label" style="left:59px;top:34px;">Front</div>
  <div class="sheet-label" style="left:622px;top:34px;">Back - 1</div>
  <div class="sheet-label" style="left:53px;top:404px;">Back - 2</div>
  <div class="sheet-label" style="left:622px;top:404px;">Back - 3</div>

  <!-- Front -->
  <section class="card card--front">
    <div class="brand-dot" style="top:18px;width:104px;height:104px;background:var(--leaf-green);"></div>
    <div class="wordmark" style="top:133px;color:var(--brand-green);">
      <span class="name" style="font-size:29px;">Marwick</span>
      <span class="trade" style="font-size:11.5px;margin-top:4px;">Family Chiropractic</span>
    </div>
    <div class="doctor">Dr. Leonard Marwick D.C., <span class="role">Chiropractor</span></div>
    <p class="contact" style="top:224px;"><b>phone</b> 555-555-0183<span class="sep">|</span><b>email</b> mymarwick@marwickspine.example</p>
    <p class="contact" style="top:244px;"><b>web</b> : www.marwickspine.example<span class="sep">|</span><b>face book</b> : MarwickFamilySpine</p>
    <p class="contact" style="top:265px;">417 Birchfield Road, 2nd Floor, Larkspur Hollow, NH 06091</p>
    <div class="color-band">
      <span style="background:var(--olive);"></span>
      <span style="background:var(--bark);"></span>
      <span style="background:var(--leaf-green);"></span>
    </div>
  </section>

  <!-- Back 1 -->
  <section class="card card--back-1">
    <div class="brand-dot" style="top:32px;width:126px;height:126px;background:var(--leaf-green);"></div>
    <div class="wordmark" style="top:170px;color:var(--brand-green);">
      <span class="name" style="font-size:34px;">Marwick</span>
      <span class="trade" style="font-size:14px;margin-top:6px;">Family Chiropractic</span>
    </div>
    <p class="web" style="top:262px;color:var(--ink);">www.marwickspine.example</p>
  </section>

  <!-- Back 2 -->
  <section class="card card--back-2">
    <div class="brand-dot" style="top:36px;width:230px;height:230px;background:rgba(255,255,255,0.05);"></div>
    <div class="wordmark" style="top:98px;color:var(--brand-green);">
      <span class="name" style="font-size:62px;letter-spacing:2px;">Marwick</span>
      <span class="trade" style="font-size:27px;margin-top:14px;letter-spacing:1px;">Family Chiropractic</span>
    </div>
    <p class="web" style="top:263px;color:#ffffff;">www.marwickspine.example</p>
  </section>

  <!-- Back 3 -->
  <section class="card card--back-3">
    <div class="brand-dot" style="top:30px;width:126px;height:126px;background:var(--leaf-green);"></div>
    <div class="wordmark" style="top:171px;color:var(--leaf-green);">
      <span class="name" style="font-size:33px;">Marwick</span>
      <span class="trade" style="font-size:13.5px;margin-top:7px;">Family Chiropractic</span>
    </div>
    <p class="web" style="top:263px;color:#ffffff;">www.marwickspine.example</p>
  </section>

</body>
</html>
```